Mental Health care Company in Washington DC

We are a new mental health care services provider in Washington DC. Please look at these sites.
https://brightwaterfamilysupport.com
https://www.quietharborinc.com
https://willowgate-dc.org/
https://www.tidepathdc.com
https://www.thelanternofdc.com

```html
<!DOCTYPE html>
<html lang="en">
<head>
<meta charset="utf-8">
<title>Rivena Health Services</title>
<link href="https://fonts.googleapis.com/css2?family=Poppins:wght@400;500;600;700&family=Montserrat:wght@400;500;600;700&display=swap" rel="stylesheet">
<style>
:root{
  --navy:#10294a;
  --teal:#86cfd4;
  --teal-light:#c9eaec;
  --orange:#f4a05d;
  --orange-deep:#f47f22;
  --white:#ffffff;
  --text:#3a4657;
  --line:#e6edf0;
}
*{box-sizing:border-box;margin:0;padding:0}
html,body{width:1200px;height:3797px;overflow:hidden}
body{position:relative;background:var(--white);font-family:"Montserrat",sans-serif;color:var(--text)}
.abs{position:absolute}
.heading{font-family:"Poppins",sans-serif;color:var(--navy);font-weight:400;line-height:1.1}
.heading b{font-weight:700}
.btn{position:absolute;display:flex;align-items:center;justify-content:center;background:var(--orange);color:var(--white);font-family:"Montserrat",sans-serif;font-weight:700;font-size:14px;letter-spacing:.3px;text-transform:uppercase}
.photo{position:absolute}
.brand{font-family:"Poppins",sans-serif;font-weight:600;color:var(--navy);white-space:nowrap}

/* header */
.site-header{position:absolute;left:0;top:0;width:1200px;height:88px;background:var(--white)}
.site-header .brand{position:absolute;left:100px;top:28px;font-size:26px}
.nav{position:absolute;top:36px;font-size:14px;color:var(--navy);font-weight:500}
.nav.active::after{content:"";position:absolute;left:0;right:0;top:24px;height:3px;background:var(--teal)}
.header-btn{left:929px;top:24px;width:187px;height:39px;background:var(--teal);font-size:11px}

/* hero */
.hero{position:absolute;left:0;top:88px;width:1200px;height:715px;overflow:hidden;background:#1f2a38}
.hero-photo{left:480px;top:0;width:720px;height:715px;background:linear-gradient(100deg,#27323f 0%,#6b7480 35%,#a5a9ab 70%,#c3c4c0 100%)}
.hero-fade{position:absolute;left:0;top:0;width:820px;height:715px;background:linear-gradient(90deg,#1e2835 55%,rgba(30,40,53,0))}
.hero h1{position:absolute;left:107px;top:196px;font-family:"Poppins",sans-serif;font-weight:400;font-size:45px;color:var(--teal);line-height:1}
.hero h1 span{display:block;color:var(--white);font-weight:600;margin-top:4px}
.hero p{position:absolute;left:112px;top:306px;width:460px;font-size:16px;line-height:26px;color:#e9edf0}
.hero .btn{left:108px;top:382px;width:231px;height:47px}
.dots{position:absolute;left:22px;top:278px;width:14px}
.dots i{display:block;width:6px;height:6px;border-radius:50%;background:#8893a0;margin:6px auto}
.dots i.cap{width:14px;height:14px;background:var(--white)}
.wave{position:absolute;left:0;width:1200px}

/* about */
.about-title{left:649px;top:910px;font-size:44px}
.rule{position:absolute;height:2px;width:54px;background:var(--orange)}
.about-text{left:650px;top:986px;width:450px;font-size:14.5px;line-height:26px}
.about-text p+p{margin-top:0}

/* services */
.services{position:absolute;left:0;top:1359px;width:1200px;height:740px;background:var(--teal-light)}
.services-title{left:0;width:1200px;top:1430px;text-align:center;font-size:42px}
.service{position:absolute;width:320px;text-align:center}
.service .ring{position:absolute;width:250px;height:250px;border-radius:50%;border:2px solid #b6dfe2}
.service .circle{position:absolute;width:218px;height:218px;border-radius:50%}
.service h3{position:absolute;left:0;width:320px;font-family:"Montserrat",sans-serif;font-weight:600;font-size:21px;color:var(--navy)}
.service p{position:absolute;left:25px;width:270px;font-size:11.5px;line-height:15px;color:var(--text)}
.service-card{position:absolute;left:446px;top:1614px;width:333px;height:374px;background:var(--white);border-radius:0 0 44px 0;box-shadow:8px 8px 0 var(--orange)}

/* treatment */
.treat-title{left:117px;top:2128px;font-size:42px}
.treat-card{position:absolute;top:2270px;width:309px;height:410px;border:2px solid #d9dee2;border-radius:16px;background:var(--white);overflow:hidden}
.treat-card .pic{position:absolute;left:0;top:0;width:100%;height:243px}
.treat-card h4{position:absolute;left:30px;top:272px;font-family:"Montserrat",sans-serif;font-size:16.5px;font-weight:700;color:var(--navy);white-space:nowrap}
.treat-card p{position:absolute;left:30px;top:302px;width:260px;font-size:15px;line-height:24px;color:var(--navy)}
.treat-card .btn{left:30px;top:354px;width:130px;height:32px;font-size:10px}

/* booking */
.booking{position:absolute;left:0;top:2812px;width:1200px;height:720px;background:var(--orange-deep)}
.book-title{left:132px;top:2905px;font-size:42px;color:var(--white)}
.book-lead{left:133px;top:2980px;font-size:15px;color:var(--white)}
.field{position:absolute;left:133px;width:449px;height:53px;background:var(--white);font-size:15px;color:var(--navy);padding:16px 24px}
.submit{left:133px;top:3315px;width:175px;height:44px;background:var(--teal-light);color:var(--navy)}

/* contact + footer */
.contact .brand{position:absolute;left:118px;top:3548px;font-size:34px}
.contact-item{position:absolute;top:3543px;display:flex;align-items:center;gap:12px}
.contact-icon{width:52px;height:52px;border-radius:50%;background:var(--teal);display:flex;align-items:center;justify-content:center}
.contact-item strong{display:block;font-size:15px;color:var(--navy);font-weight:700}
.contact-item span{font-size:15px;color:var(--navy)}
.footer-line{position:absolute;left:0;top:3658px;width:1200px;height:2px;background:var(--line)}
.foot-nav{position:absolute;top:3697px;font-size:15.5px;font-weight:600;color:var(--navy)}
.copyright{position:absolute;left:125px;top:3744px;font-size:11px;color:var(--navy)}
.social{position:absolute;top:3694px;width:26px;height:26px;border-radius:50%;background:var(--orange-deep)}
</style>
</head>
<body>

<header class="site-header">
  <div class="brand">Rivena Health Services</div>
  <div class="nav active" style="left:402px">HOME</div>
  <div class="nav" style="left:491px">SERVICES</div>
  <div class="nav" style="left:607px">ABOUT US</div>
  <div class="nav" style="left:728px">WHY US</div>
  <div class="nav" style="left:833px">CONTACT</div>
  <div class="btn header-btn">Book Appointment &rsaquo;</div>
</header>

<section class="hero">
  <div class="photo hero-photo" role="img" aria-label="Smiling bearded man in a light shirt seated in a bright room"></div>
  <div class="hero-fade"></div>
  <div class="dots"><i class="cap"></i><i></i><i></i><i></i><i class="cap"></i></div>
  <h1>Welcome to<span>Rivena Health Services</span></h1>
  <p>Lorem ipsum dolor sit amet, consectetur adipiscing elit, sed do eiusmod tempor incididunt ut labore</p>
  <div class="btn">Book Appointment &nbsp;&rsaquo;</div>
  <svg class="abs" style="left:588px;top:592px" width="30" height="36" viewBox="0 0 30 36"><path d="M15 2v30M3 20l12 12 12-12" fill="none" stroke="#fff" stroke-width="3"/></svg>
  <svg class="wave" style="top:610px" width="1200" height="105" viewBox="0 0 1200 105" preserveAspectRatio="none">
    <path d="M0 140 L0 58 C180 -10 420 5 700 70 C900 110 1080 95 1200 78 L1200 140Z" fill="var(--teal)"/>
    <path d="M0 140 L0 72 C180 10 420 22 700 86 C900 125 1080 110 1200 95 L1200 140Z" fill="#fff"/>
  </svg>
</section>

<section class="about">
  <div class="photo" style="left:108px;top:865px;width:242px;height:160px;border-radius:80px 0 0 80px;background:linear-gradient(135deg,#c9c3bb,#6f7a86)" role="img" aria-label="Counsellor talking with a client"></div>
  <div class="photo" style="left:366px;top:786px;width:160px;height:242px;border-radius:80px 80px 80px 0;background:linear-gradient(160deg,#8d8a84,#4b4f55)" role="img" aria-label="Woman listening in a session"></div>
  <div class="photo" style="left:108px;top:1050px;width:242px;height:203px;border-radius:0 0 0 100px;background:linear-gradient(135deg,#d8d2c8,#7c8b9a)" role="img" aria-label="Young man talking in a therapy session"></div>
  <div class="photo" style="left:375px;top:1050px;width:219px;height:178px;border-radius:0 100px 100px 100px;background:linear-gradient(135deg,#cfcfcc,#7d8893)" role="img" aria-label="Man speaking with a therapist"></div>
  <h2 class="heading abs about-title">About <b>Rivena Health</b></h2>
  <div class="rule" style="left:650px;top:964px"></div>
  <div class="abs about-text">
    <p>Lorem ipsum dolor sit amet, consectetur adipiscing elit, sed do eiusmod tempor incididunt ut labore et dolore magna aliqua. Ut enim ad minim veniam, quis nostrud exercitation ullamco laboris nisi ut aliquip ex ea commodo co</p>
    <p>Lorem ipsum dolor sit amet, consectetur adipiscing elit, sed do eiusmod tempor incididunt ut labore et dolore magna aliqua. Ut enim ad minim veniam, quis nostrud</p>
  </div>
  <div class="btn" style="left:649px;top:1198px;width:175px;height:44px">Learn More &rsaquo;</div>
</section>

<section class="services">
  <svg class="wave" style="top:670px" width="1200" height="72" viewBox="0 0 1200 72" preserveAspectRatio="none">
    <path d="M0 38 C260 -10 520 20 760 38 C960 52 1100 40 1200 28 L1200 72 L0 72Z" fill="#fff"/>
  </svg>
</section>
<h2 class="heading abs services-title">Services <b>Provide</b></h2>
<div class="rule" style="left:580px;top:1482px;width:50px"></div>

<div class="service-card"></div>

<div class="service" style="left:120px;top:1520px">
  <div class="ring" style="left:30px;top:0"></div>
  <div class="circle" style="left:46px;top:16px;background:linear-gradient(135deg,#b9b7b3,#55585d)" role="img" aria-label="Woman with eyes closed, hands on chest"></div>
  <h3 style="top:274px">BEHAVIORAL HEALTH</h3>
  <p style="top:310px">Lorem ipsum dolor sit amet, consectetur adipiscing elit, sed do eiusmod tempor incididunt ut labore et dolor</p>
  <div class="btn" style="left:68px;top:375px;width:175px;height:42px">Learn More &rsaquo;</div>
</div>

<div class="service" style="left:453px;top:1514px">
  <div class="ring" style="left:30px;top:0"></div>
  <div class="circle" style="left:46px;top:16px;background:linear-gradient(135deg,#c8cdd1,#5c7b96)" role="img" aria-label="Man in a session with a clipboard"></div>
  <h3 style="top:280px">MENTAL CARE</h3>
  <p style="top:316px">Lorem ipsum dolor sit amet, consectetur adipiscing elit, sed do eiusmod tempor incididunt ut labore et dolor</p>
  <div class="btn" style="left:77px;top:378px;width:175px;height:42px">Learn More &rsaquo;</div>
</div>

<div class="service" style="left:786px;top:1514px">
  <div class="ring" style="left:30px;top:0"></div>
  <div class="circle" style="left:46px;top:16px;background:linear-gradient(135deg,#dcd6cc,#6f8b6a)" role="img" aria-label="Caregiver holding hands with a woman in a wheelchair"></div>
  <h3 style="top:280px">MEDICAL SERVICES</h3>
  <p style="top:316px">Lorem ipsum dolor sit amet, consectetur adipiscing elit, sed do eiusmod tempor incididunt ut labore et dolor</p>
  <div class="btn" style="left:77px;top:376px;width:175px;height:42px">Learn More &rsaquo;</div>
</div>

<h2 class="heading abs treat-title">Our Treatment<br><b>Approach and Therapy</b></h2>
<div class="rule" style="left:118px;top:2232px"></div>

<div class="treat-card" style="left:110px">
  <div class="pic" role="img" aria-label="Therapist taking notes in an armchair" style="background:linear-gradient(135deg,#5b4a3c,#b49c82)"></div>
  <h4>Therapy Title here</h4>
  <p>Lorem ipsum dolor sit amet, consectetur adipiscing elit</p>
  <div class="btn">Learn More &rsaquo;</div>
</div>
<div class="treat-card" style="left:440px;top:2266px">
  <div class="pic" role="img" aria-label="Two people in a session with a clipboard" style="background:linear-gradient(135deg,#c99a78,#7a3e2b)"></div>
  <h4>Therapy Title here</h4>
  <p>Lorem ipsum dolor sit amet, consectetur adipiscing elit</p>
  <div class="btn">Learn More &rsaquo;</div>
</div>
<div class="treat-card" style="left:774px;top:2266px">
  <div class="pic" role="img" aria-label="Group therapy circle offering support" style="background:linear-gradient(135deg,#d9d2c6,#4f5b5a)"></div>
  <h4>Therapy Title here</h4>
  <p>Lorem ipsum dolor sit amet, consectetur adipiscing elit</p>
  <div class="btn">Learn More &rsaquo;</div>
</div>
<div class="treat-card" style="left:1105px;top:2266px">
  <div class="pic" role="img" aria-label="Client speaking with a counsellor" style="background:linear-gradient(135deg,#e0d7cb,#8a6e5a)"></div>
  <h4>Therapy Title here</h4>
  <p>Lorem ipsum dolor sit amet, consectetur adipiscing elit</p>
  <div class="btn">Learn More &rsaquo;</div>
</div>

<section class="booking">
  <svg class="wave" style="top:575px" width="1200" height="150" viewBox="0 0 1200 150" preserveAspectRatio="none">
    <path d="M0 90 C250 130 500 150 760 110 C980 75 1120 40 1200 0 L1200 150 L0 150Z" fill="var(--teal-light)"/>
    <path d="M0 112 C250 150 500 168 760 132 C980 100 1120 60 1200 22 L1200 150 L0 150Z" fill="#fff"/>
  </svg>
</section>
<h2 class="heading abs book-title">Book an <b>Appointment</b></h2>
<p class="abs book-lead">Lorem ipsum dolor sit amet, consectetur adipiscing elit,</p>
<div class="field" style="top:3022px">Your Name</div>
<div class="field" style="top:3085px">Email address</div>
<div class="field" style="top:3148px">Phone Number</div>
<div class="field" style="top:3211px;height:90px">Message</div>
<div class="btn submit">Submit Now &rsaquo;</div>
<div class="photo" style="left:625px;top:3022px;width:237px;height:376px;border-radius:110px 0 110px 110px;background:linear-gradient(160deg,#d7ccc2,#8d7f76)" role="img" aria-label="Hands resting on a clipboard during a consultation"></div>
<div class="photo" style="left:876px;top:2882px;width:235px;height:372px;border-radius:110px 110px 110px 0;background:linear-gradient(160deg,#5b6a44,#a7a77e)" role="img" aria-label="Happy woman stretching outdoors"></div>

<section class="contact">
  <div class="brand">Rivena Health</div>
  <div class="contact-item" style="left:375px">
    <div class="contact-icon"><svg width="24" height="24" viewBox="0 0 24 24"><path d="M6.6 10.8a15 15 0 0 0 6.6 6.6l2.2-2.2c.3-.3.7-.4 1-.2 1.1.4 2.3.6 3.6.6.6 0 1 .4 1 1V20c0 .6-.4 1-1 1A17 17 0 0 1 3 4c0-.6.4-1 1-1h3.5c.6 0 1 .4 1 1 0 1.3.2 2.5.6 3.6.1.3 0 .7-.2 1z" fill="#fff"/></svg></div>
    <div><strong>Phone Number</strong><span>(202) 555-0148</span></div>
  </div>
  <div class="contact-item" style="left:576px">
    <div class="contact-icon"><svg width="24" height="24" viewBox="0 0 24 24"><rect x="3" y="5" width="18" height="14" rx="2" fill="#fff"/><path d="M3 7l9 6 9-6" fill="none" stroke="var(--teal)" stroke-width="2"/></svg></div>
    <div><strong>Email address</strong><span>hello@rivenahealth.example</span></div>
  </div>
  <div class="contact-item" style="left:861px">
    <div class="contact-icon"><svg width="24" height="24" viewBox="0 0 24 24"><path d="M12 2a7 7 0 0 0-7 7c0 5 7 13 7 13s7-8 7-13a7 7 0 0 0-7-7zm0 9.5A2.5 2.5 0 1 1 12 6.5a2.5 2.5 0 0 1 0 5z" fill="#fff"/></svg></div>
    <div><strong>Location</strong><span>1st Floor 2210 Linden Street</span></div>
  </div>
</section>

<div class="footer-line"></div>
<footer>
  <div class="foot-nav" style="left:125px">HOME</div>
  <div class="foot-nav" style="left:235px">SERVICES</div>
  <div class="foot-nav" style="left:373px">ABOUT US</div>
  <div class="foot-nav" style="left:516px">WHY US</div>
  <div class="foot-nav" style="left:641px">CONTACT US</div>
  <div class="social" style="left:893px" aria-label="Social link"></div>
  <div class="social" style="left:951px" aria-label="Social link"></div>
  <div class="social" style="left:1008px" aria-label="Social link"></div>
  <div class="social" style="left:1066px" aria-label="Social link"></div>
  <div class="copyright">© 2025 Company Name | All Rights Reserved</div>
</footer>

</body>
</html>
```